Business Card - connecting 2 souls and beggining the journey of self discovery

Logo on the front
with tag line

On the back list of services and contact details

Seminars
workshops
Coaching
podcasts

Darren Whitlow
Health & Wellbeing Life Coach
0491 372 615
darren@brightcoreliving.example
brightcoreliving.example

Industry/Entity Type

Life Coaching

Contact Information for Business Card

I like the use of colour from the logo to be used. I'm not a fan of white.

Requirements
Must have
• My tagline: Every path inward begins here
Nice to have
• Use of colour that is in the mind body soul logo

```html
<!DOCTYPE html>
<html lang="en">
<head>
<meta charset="utf-8">
<title>Bright Core Living – Business Card</title>
<link rel="stylesheet" href="https://fonts.googleapis.com/css2?family=Questrial&display=swap">
<style>
  :root {
    --backdrop: #2a2a2c;
    --grad-pink: #f6a4a6;
    --grad-orange: #f29a52;
    --grad-coral: #ee5f68;
    --slate: #98999c;
    --paper: #f4f4f3;
    --ink-grey: #6b6c6f;
    --white: #ffffff;
    --mark: #f28a4e;
    --band-purple: #9a4fb8;
    --band-green: #6cc26a;
    --band-orange: #f2a24a;
    --band-pink: #ec5f79;
  }
  * { box-sizing: border-box; margin: 0; padding: 0; }
  html, body {
    width: 1200px; height: 900px; overflow: hidden;
    background: var(--backdrop);
    font-family: "Questrial", "Century Gothic", sans-serif;
  }
  .card {
    position: absolute; left: 250px; width: 700px; height: 400px;
    overflow: hidden; border-radius: 4px;
  }
  /* Front */
  .card-front {
    top: 40px;
    background: linear-gradient(125deg, var(--grad-pink) 0%, var(--grad-orange) 48%, var(--grad-coral) 100%);
    color: var(--white);
    display: flex; flex-direction: column; align-items: center; justify-content: center;
  }
  .brand-mark {
    width: 96px; height: 96px; border-radius: 50%;
    background: var(--mark);
    border: 3px solid var(--white);
    margin-bottom: 26px;
  }
  .brand-name { font-size: 40px; font-weight: 400; letter-spacing: -0.5px; }
  .service-list {
    list-style: none; display: flex; gap: 10px; margin-top: 28px; font-size: 16px;
  }
  .service-list li + li::before { content: "•"; margin-right: 10px; }

  /* Back */
  .card-back { top: 470px; background: var(--slate); }
  .card-back svg { position: absolute; inset: 0; }
  .contact {
    position: absolute; right: 445px; top: 175px; width: 250px;
    color: var(--white); text-align: right;
  }
  .contact-name { font-size: 22px; }
  .contact-role { font-size: 16px; margin-top: 4px; }
  .contact-lines { list-style: none; font-size: 14px; margin-top: 12px; line-height: 1.45; }
  .back-brand {
    position: absolute; left: 330px; top: 92px; color: var(--ink-grey);
  }
  .back-brand .brand-name { font-size: 28px; }
  .tagline { font-size: 15px; margin-top: 4px; }
  .back-mark {
    position: absolute; left: 590px; top: 82px;
    width: 80px; height: 80px; border-radius: 50%; background: var(--mark);
  }
</style>
</head>
<body>
  <section class="card card-front">
    <div class="brand-mark"></div>
    <h1 class="brand-name">Bright Core Living</h1>
    <ul class="service-list">
      <li>Seminars</li><li>Workshops</li><li>Coaching</li><li>Podcasts</li>
    </ul>
  </section>

  <section class="card card-back">
    <svg width="700" height="400" viewBox="0 0 700 400" aria-hidden="true">
      <circle cx="700" cy="-30" r="470" fill="var(--paper)"/>
      <g fill="none" stroke-width="9">
        <path d="M231 0 A470 470 0 0 0 255.6 123" stroke="var(--band-purple)"/>
        <path d="M255.6 123 A470 470 0 0 0 315 239.6" stroke="var(--band-green)"/>
        <path d="M315 239.6 A470 470 0 0 0 397.9 330" stroke="var(--band-orange)"/>
        <path d="M397.9 330 A470 470 0 0 0 510.4 400" stroke="var(--band-pink)"/>
      </g>
    </svg>
    <div class="back-brand">
      <h2 class="brand-name">Bright Core Living</h2>
      <p class="tagline">Every path inward begins here</p>
    </div>
    <div class="back-mark"></div>
    <div class="contact">
      <p class="contact-name">Darren Whitlow</p>
      <p class="contact-role">Health &amp; Wellbeing Life Coach</p>
      <ul class="contact-lines">
        <li>P : 0491 372 615</li>
        <li>darren@brightcoreliving.example</li>
        <li>brightcoreliving.example</li>
      </ul>
    </div>
  </section>
</body>
</html>
```